Before the kettle boils, pocast with content in its majority of technology

Page dedicated to a pocast with content in its majority of technology. The page also contains the chapters of the podcast (pluggin vocalink) will also contain news. Preferably Worpress. There is already a very basic page with a simple theme, the logo and little more, I would like something more professional. Www.lamparadebolsillo.com The logo does not want to change.

Target Market(s)

Anyone

Colors

Designer to choose colors to be used in the design.

Requirements
Must have
• You can put the vocalink pluggin with the podcast chapters

```html
<!DOCTYPE html>
<html lang="es">
<head>
<meta charset="utf-8">
<title>Before the kettle boils — Podcast de tecnología</title>
<link rel="stylesheet" href="https://fonts.googleapis.com/css2?family=Open+Sans:ital,wght@0,400;0,600;0,700;1,400&family=Poppins:wght@400;500;600&family=Roboto:wght@500;700&display=swap">
<style>
:root{
  --orange:#f26a1b;
  --orange-light:#ff9a1a;
  --orange-deep:#e9501a;
  --dark:#1d1d1d;
  --dark-2:#262626;
  --wood:#5a4535;
  --wood-dark:#3b2c21;
  --text:#444;
  --muted:#777;
  --line:#e4e4e4;
  --white:#fff;
}
*{box-sizing:border-box;margin:0;padding:0}
html,body{width:1200px;height:2459px;overflow:hidden}
body{background:linear-gradient(90deg,var(--wood-dark),var(--wood) 8%,var(--wood) 92%,var(--wood-dark));font-family:"Open Sans",sans-serif;color:var(--text);position:relative}
.page{position:absolute;left:92px;top:0;width:1016px;height:2459px;background:var(--white);overflow:hidden}
.abs{position:absolute}

/* header */
.header{left:0;top:0;width:1016px;height:154px;background:radial-gradient(ellipse at 50% 0,#333,var(--dark) 70%)}
.social-top{left:23px;top:70px;display:flex;gap:6px}
.social-top span{width:19px;height:19px;border-radius:50%;display:block}
.brand{left:358px;top:26px;width:300px;text-align:center}
.brand-dot{width:58px;height:58px;border-radius:50%;border:5px solid var(--orange);margin:0 auto 8px}
.brand-name{font-family:"Poppins",sans-serif;font-weight:600;font-size:14px;color:var(--orange);text-transform:uppercase;letter-spacing:.5px;white-space:nowrap}
.search-top{left:800px;top:57px;width:190px;height:30px;border:2px solid #ddd;border-radius:16px;color:#ccc;font-size:12px;padding:5px 14px}
.search-top svg{position:absolute;right:10px;top:7px}

.nav{left:0;top:154px;width:1016px;height:46px;background:linear-gradient(var(--orange-light),var(--orange-deep));display:flex;justify-content:center}
.nav a{font-family:"Poppins",sans-serif;font-weight:500;font-size:14.5px;color:var(--white);text-decoration:none;padding:0 24px;line-height:46px;border-left:1px solid rgba(0,0,0,.12)}
.nav a:first-child{border-left:none}

.hero{left:0;top:200px;width:1016px;height:429px;background:linear-gradient(180deg,#b8c1cc,#8d96a3 60%,#6d6b6e);overflow:hidden}
.hero-person{left:120px;top:0;width:320px;height:429px;background:linear-gradient(180deg,#4a4a55,#7a4a55 50%,#5a3a48);border-radius:140px 140px 0 0}
.hero-copy{left:668px;top:128px;width:340px}
.hero-copy h1{font-family:"Roboto",sans-serif;font-weight:700;font-size:38px;line-height:41px;color:#222;text-transform:uppercase}
.hero-copy p{font-size:13px;line-height:22px;color:#222;margin-top:10px}
.btn-more{display:inline-block;margin-top:20px;background:var(--orange-deep);color:var(--white);font-size:10px;font-weight:700;padding:7px 13px;border-radius:2px;text-transform:uppercase}
.dots{left:670px;top:330px;display:flex;gap:6px;align-items:center}
.dots span{width:11px;height:11px;border-radius:50%;background:var(--white)}
.dots span:first-child{width:15px;height:15px;border:2px solid #bbb}

/* posts */
.post{left:23px;width:662px}
.player{position:relative;height:66px;border-top:3px solid #333;background:linear-gradient(90deg,var(--orange),var(--orange-light));display:flex;align-items:center}
.player-thumb{width:77px;height:63px;background:linear-gradient(135deg,#9a8f88,#4c4846)}
.player-title{padding-left:18px;color:var(--white);flex:1}
.player-title b{display:block;font-family:"Poppins",sans-serif;font-weight:400;font-size:21px;line-height:24px}
.player-title small{font-size:13px;font-weight:700}
.player-ctrl{display:flex;align-items:center;height:100%}
.player-ctrl span{height:100%;display:flex;align-items:center;padding:0 10px;border-left:1px solid rgba(255,255,255,.35)}
.post h2{font-family:"Poppins",sans-serif;font-weight:400;font-size:21px;color:#333;margin-top:28px}
.meta{display:flex;font-size:10.5px;font-style:italic;color:var(--muted);margin-top:12px}
.meta span{display:flex;align-items:center;gap:6px;padding-right:18px;margin-right:18px;border-right:1px solid var(--line)}
.meta span:last-child{border:none}
.excerpt{font-size:11.5px;line-height:20px;color:#555;margin-top:12px}
.share{display:flex;gap:4px;margin-top:14px}
.share i{width:21px;height:21px;border-radius:50%;display:block}
.continue{font-size:10.5px;color:var(--orange-deep);text-transform:uppercase;margin-top:17px;font-weight:600}

/* sidebar */
.side{left:737px;width:253px}
.side-search{top:688px;height:40px;border:1px solid #ccc;font-size:11px;color:#666;padding:12px 14px}
.side-search svg{position:absolute;right:14px;top:13px}
.top10{top:754px;height:167px;background:linear-gradient(135deg,#555,#222);color:var(--white);font-family:"Roboto",sans-serif;font-weight:700;font-size:28px;line-height:31px;padding:86px 0 0 18px}
.widget-title{height:40px;font-family:"Poppins",sans-serif;font-weight:600;font-size:18px;color:var(--white);border-bottom:2px solid var(--orange)}
.widget-title span{display:inline-block;height:38px;line-height:38px;padding:0 38px 0 14px;background:linear-gradient(90deg,var(--orange),var(--orange-light));clip-path:polygon(0 0,82% 0,100% 100%,0 100%)}
.recent{display:flex;gap:18px;height:157px;border-bottom:1px solid var(--line)}
.recent-thumb{width:95px;height:102px;flex:none}
.recent h4{font-weight:400;font-size:12.5px;color:#444}
.stars{color:var(--orange);font-size:10px;margin:4px 0 6px;letter-spacing:1px}
.recent p{font-size:10.5px;line-height:17px;color:#555}
.recent em{display:block;font-size:10px;color:#666;margin-top:6px}
.contact-list{list-style:none;font-size:13px;color:#444}
.contact-list li{height:30px;display:flex;align-items:center;gap:10px}
.tiles{display:grid;grid-template-columns:repeat(3,77px);gap:8px;row-gap:7px}
.tile{height:75px;color:var(--white);text-align:center;font-size:12.5px;line-height:15px;padding-top:12px}
.tile i{display:block;width:20px;height:20px;border-radius:50%;background:rgba(255,255,255,.85);margin:0 auto 6px}

/* footer */
.footer{left:0;top:2083px;width:1016px;height:376px}
.footer h3{font-family:"Poppins",sans-serif;font-weight:500;font-size:17px;color:var(--white);text-transform:uppercase}
.f-text{font-size:12.5px;color:#ddd;line-height:20px}
.f-row{display:flex;gap:16px;align-items:flex-start;margin-top:14px}
.f-input{width:276px;height:40px;background:var(--white);font-size:10px;color:#555;padding:13px 12px;margin-top:14px}
.f-btn{display:inline-block;margin-top:15px;background:linear-gradient(var(--orange-light),var(--orange-deep));color:var(--white);font-size:11px;font-weight:700;padding:13px 14px;text-transform:uppercase}
.f-links{list-style:none;font-size:11.5px;color:#eee;line-height:23px;margin-top:12px}
.f-brand{left:816px;top:103px;width:200px;text-align:center}
.f-brand .brand-name{font-size:13px;letter-spacing:0}
.copyright{left:0;top:340px;width:1016px;text-align:center;font-size:11.5px;color:#ddd}
</style>
</head>
<body>
<div class="page">

  <header class="abs header">
    <div class="abs social-top">
      <span style="background:#3b5998"></span><span style="background:#f7a21b"></span><span style="background:#1da1f2"></span><span style="background:#26a7c7"></span><span style="background:#d6332a"></span>
    </div>
    <div class="abs brand">
      <div class="brand-dot"></div>
      <div class="brand-name">Before the kettle boils</div>
    </div>
    <div class="abs search-top">search
      <svg width="12" height="12" viewBox="0 0 12 12"><circle cx="5" cy="5" r="3.6" fill="none" stroke="#fff" stroke-width="1.8"/><line x1="7.6" y1="7.6" x2="11" y2="11" stroke="#fff" stroke-width="1.8"/></svg>
    </div>
  </header>

  <nav class="abs nav">
    <a>HOME</a><a>ABOUT US</a><a>PODCAST</a><a>RECENT POSTS</a><a>BLOG</a><a>CONTACT US</a>
  </nav>

  <section class="abs hero" role="img" aria-label="Photo of a smiling man with headphones and a phone in front of a city skyline">
    <div class="abs hero-person"></div>
    <div class="abs hero-copy">
      <h1>Before the<br>kettle boils</h1>
      <p>Sed ut perspiciatis unde omnis iste natus error sit voluptatem accusantium doloremque</p>
      <span class="btn-more">Read more ›</span>
    </div>
    <div class="abs dots"><span></span><span></span><span></span><span></span></div>
  </section>

  <!-- posts -->
  <article class="abs post" style="top:685px">
    <div class="player"><div class="player-thumb" role="img" aria-label="Episode thumbnail photo"></div>
      <div class="player-title"><b>Cambio de logo</b><small>Hola a Tod@s!</small></div>
      <div class="player-ctrl">
        <span><svg width="18" height="18" viewBox="0 0 18 18" fill="none" stroke="#fff" stroke-width="1.5"><circle cx="4" cy="9" r="2.2"/><circle cx="14" cy="4" r="2.2"/><circle cx="14" cy="14" r="2.2"/><path d="M6 8l6-3M6 10l6 3"/></svg></span>
        <span><svg width="18" height="18" viewBox="0 0 18 18" fill="none" stroke="#fff" stroke-width="1.5"><path d="M9 2v10M5 8l4 4 4-4M2 15h14"/></svg></span>
        <span><svg width="28" height="28" viewBox="0 0 28 28" fill="none" stroke="#fff" stroke-width="2"><circle cx="14" cy="14" r="12"/><path d="M11 9l7 5-7 5z" fill="#fff"/></svg></span>
      </div>
    </div>
    <h2>Sed ut perspiciatis unde omnis iste natus</h2>
    <div class="meta"><span>▪ March 25, 2017</span><span>▫ 2 comments</span><span>✎ by Marco</span></div>
    <p class="excerpt">¿Salta a la vista no?, pues sí, renovamos diseño del logo y algo en la web. Aquí los cambios irán poco a poco pero procuraré dejar todo lo que quiero modificar hecho en una semana como mucho, todo dependerá del tiempo que le pueda dedicar aunque lo difícil ya está hecho. Nada más, nos escuchamos en el siguiente!</p>
    <div class="share"><i style="background:#1da1f2"></i><i style="background:#3b5998"></i><i style="background:#dd4b39"></i><i style="background:#cfe0f3"></i><i style="background:#0e76a8"></i><i style="background:#2ca5e0"></i><i style="background:#25d366"></i><i style="background:#ef4056"></i><i style="background:#bbb"></i><i style="background:#ddd"></i></div>
    <div class="continue">Continue reading &gt;&gt;</div>
  </article>

  <article class="abs post" style="top:1024px">
    <div class="player"><div class="player-thumb" role="img" aria-label="Episode thumbnail photo"></div>
      <div class="player-title"><b>Cambio de logo</b><small>Hola a Tod@s!</small></div>
      <div class="player-ctrl">
        <span><svg width="18" height="18" viewBox="0 0 18 18" fill="none" stroke="#fff" stroke-width="1.5"><circle cx="4" cy="9" r="2.2"/><circle cx="14" cy="4" r="2.2"/><circle cx="14" cy="14" r="2.2"/><path d="M6 8l6-3M6 10l6 3"/></svg></span>
        <span><svg width="18" height="18" viewBox="0 0 18 18" fill="none" stroke="#fff" stroke-width="1.5"><path d="M9 2v10M5 8l4 4 4-4M2 15h14"/></svg></span>
        <span><svg width="28" height="28" viewBox="0 0 28 28" fill="none" stroke="#fff" stroke-width="2"><circle cx="14" cy="14" r="12"/><path d="M11 9l7 5-7 5z" fill="#fff"/></svg></span>
      </div>
    </div>
    <h2>Sed ut perspiciatis unde omnis iste natus</h2>
    <div class="meta"><span>▪ March 25, 2017</span><span>▫ 2 comments</span><span>✎ by Marco</span></div>
    <p class="excerpt">¿Salta a la vista no?, pues sí, renovamos diseño del logo y algo en la web. Aquí los cambios irán poco a poco pero procuraré dejar todo lo que quiero modificar hecho en una semana como mucho, todo dependerá del tiempo que le pueda dedicar aunque lo difícil ya está hecho. Nada más, nos escuchamos en el siguiente!</p>
    <div class="share"><i style="background:#1da1f2"></i><i style="background:#3b5998"></i><i style="background:#dd4b39"></i><i style="background:#cfe0f3"></i><i style="background:#0e76a8"></i><i style="background:#2ca5e0"></i><i style="background:#25d366"></i><i style="background:#ef4056"></i><i style="background:#bbb"></i><i style="background:#ddd"></i></div>
    <div class="continue">Continue reading &gt;&gt;</div>
  </article>

  <article class="abs post" style="top:1363px">
    <div class="player"><div class="player-thumb" role="img" aria-label="Episode thumbnail photo"></div>
      <div class="player-title"><b>Cambio de logo</b><small>Hola a Tod@s!</small></div>
      <div class="player-ctrl">
        <span><svg width="18" height="18" viewBox="0 0 18 18" fill="none" stroke="#fff" stroke-width="1.5"><circle cx="4" cy="9" r="2.2"/><circle cx="14" cy="4" r="2.2"/><circle cx="14" cy="14" r="2.2"/><path d="M6 8l6-3M6 10l6 3"/></svg></span>
        <span><svg width="18" height="18" viewBox="0 0 18 18" fill="none" stroke="#fff" stroke-width="1.5"><path d="M9 2v10M5 8l4 4 4-4M2 15h14"/></svg></span>
        <span><svg width="28" height="28" viewBox="0 0 28 28" fill="none" stroke="#fff" stroke-width="2"><circle cx="14" cy="14" r="12"/><path d="M11 9l7 5-7 5z" fill="#fff"/></svg></span>
      </div>
    </div>
    <h2>Sed ut perspiciatis unde omnis iste natus</h2>
    <div class="meta"><span>▪ March 25, 2017</span><span>▫ 2 comments</span><span>✎ by Marco</span></div>
    <p class="excerpt">¿Salta a la vista no?, pues sí, renovamos diseño del logo y algo en la web. Aquí los cambios irán poco a poco pero procuraré dejar todo lo que quiero modificar hecho en una semana como mucho, todo dependerá del tiempo que le pueda dedicar aunque lo difícil ya está hecho. Nada más, nos escuchamos en el siguiente!</p>
    <div class="share"><i style="background:#1da1f2"></i><i style="background:#3b5998"></i><i style="background:#dd4b39"></i><i style="background:#cfe0f3"></i><i style="background:#0e76a8"></i><i style="background:#2ca5e0"></i><i style="background:#25d366"></i><i style="background:#ef4056"></i><i style="background:#bbb"></i><i style="background:#ddd"></i></div>
    <div class="continue">Continue reading &gt;&gt;</div>
  </article>

  <article class="abs post" style="top:1702px">
    <div class="player"><div class="player-thumb" role="img" aria-label="Episode thumbnail photo"></div>
      <div class="player-title"><b>Cambio de logo</b><small>Hola a Tod@s!</small></div>
      <div class="player-ctrl">
        <span><svg width="18" height="18" viewBox="0 0 18 18" fill="none" stroke="#fff" stroke-width="1.5"><circle cx="4" cy="9" r="2.2"/><circle cx="14" cy="4" r="2.2"/><circle cx="14" cy="14" r="2.2"/><path d="M6 8l6-3M6 10l6 3"/></svg></span>
        <span><svg width="18" height="18" viewBox="0 0 18 18" fill="none" stroke="#fff" stroke-width="1.5"><path d="M9 2v10M5 8l4 4 4-4M2 15h14"/></svg></span>
        <span><svg width="28" height="28" viewBox="0 0 28 28" fill="none" stroke="#fff" stroke-width="2"><circle cx="14" cy="14" r="12"/><path d="M11 9l7 5-7 5z" fill="#fff"/></svg></span>
      </div>
    </div>
    <h2>Sed ut perspiciatis unde omnis iste natus</h2>
    <div class="meta"><span>▪ March 25, 2017</span><span>▫ 2 comments</span><span>✎ by Marco</span></div>
    <p class="excerpt">¿Salta a la vista no?, pues sí, renovamos diseño del logo y algo en la web. Aquí los cambios irán poco a poco pero procuraré dejar todo lo que quiero modificar hecho en una semana como mucho, todo dependerá del tiempo que le pueda dedicar aunque lo difícil ya está hecho. Nada más, nos escuchamos en el siguiente!</p>
    <div class="share"><i style="background:#1da1f2"></i><i style="background:#3b5998"></i><i style="background:#dd4b39"></i><i style="background:#cfe0f3"></i><i style="background:#0e76a8"></i><i style="background:#2ca5e0"></i><i style="background:#25d366"></i><i style="background:#ef4056"></i><i style="background:#bbb"></i><i style="background:#ddd"></i></div>
    <div class="continue">Continue reading &gt;&gt;</div>
  </article>

  <!-- sidebar -->
  <div class="abs side side-search">SEARCH
    <svg width="12" height="12" viewBox="0 0 12 12"><circle cx="5" cy="5" r="3.6" fill="none" stroke="#555" stroke-width="1.8"/><line x1="7.6" y1="7.6" x2="11" y2="11" stroke="#555" stroke-width="1.8"/></svg>
  </div>
  <div class="abs side top10" role="img" aria-label="Studio microphone photo banner">TOP 10<br>PODCAST</div>

  <div class="abs side widget-title" style="top:955px"><span>RECENT POSTS</span></div>
  <div class="abs side" style="top:1027px">
    <div class="recent"><div class="recent-thumb" role="img" aria-label="Mixing desk photo" style="background:linear-gradient(135deg,#7f8a80,#3a3f3c)"></div>
      <div><h4>Nemo enim ipsam</h4><div class="stars">★★★☆☆</div><p>Lorem ipsum dolor sit amet, consectetur adipiscing elit.</p><em>▫ 2 comments</em></div></div>
    <div class="recent"><div class="recent-thumb" role="img" aria-label="Phone and headphones photo" style="background:linear-gradient(135deg,#d8b9a8,#8b5a4a)"></div>
      <div><h4>Nemo enim ipsam</h4><div class="stars">★★★☆☆</div><p>Lorem ipsum dolor sit amet, consectetur adipiscing elit.</p><em>▫ 2 comments</em></div></div>
    <div class="recent" style="border:none"><div class="recent-thumb" role="img" aria-label="Person listening with headphones photo" style="background:linear-gradient(135deg,#c8883a,#3a2418)"></div>
      <div><h4>Nemo enim ipsam</h4><div class="stars">★★★☆☆</div><p>Lorem ipsum dolor sit amet, consectetur adipiscing elit.</p><em>▫ 2 comments</em></div></div>
  </div>

  <div class="abs side widget-title" style="top:1502px"><span>CONTACTO</span></div>
  <ul class="abs side contact-list" style="top:1558px">
    <li>›&nbsp; Chirper</li><li>›&nbsp; vocalink</li><li>›&nbsp; Podwell</li><li>›&nbsp; Mail</li>
  </ul>
  <div class="abs side tiles" style="top:1711px">
    <div class="tile" style="background:#3b5998"><i></i>68,876<br>Fans</div>
    <div class="tile" style="background:#1da1f2"><i></i>65<br>Followers</div>
    <div class="tile" style="background:#dd4b39"><i></i>8,961<br>Followers</div>
    <div class="tile" style="background:#0e76a8"><i></i>68,876<br>Fans</div>
    <div class="tile" style="background:#cc181e"><i></i>65<br>Followers</div>
    <div class="tile" style="background:#4a7fd6"><i></i>8,961<br>Followers</div>
  </div>

  <!-- footer -->
  <footer class="abs footer">
    <svg class="abs" style="left:0;top:0" width="1016" height="376" viewBox="0 0 1016 376" preserveAspectRatio="none">
      <path d="M0 20 Q508 -6 1016 20 V376 H0 Z" fill="var(--dark-2)"/>
      <path d="M0 20 Q508 -6 1016 20" fill="none" stroke="var(--orange-light)" stroke-width="3"/>
    </svg>
    <div class="abs" style="left:23px;top:77px;width:260px">
      <h3>Contact us</h3>
      <div class="f-row"><svg width="14" height="18" viewBox="0 0 14 18" fill="none" stroke="#fff" stroke-width="1.4"><path d="M7 17s6-6.5 6-10.5A6 6 0 0 0 1 6.5C1 10.5 7 17 7 17z"/><circle cx="7" cy="6.5" r="2"/></svg>
        <p class="f-text">24044 Kettle Lane.<br>Dunmore, TX 77000</p></div>
      <div class="f-row"><svg width="16" height="16" viewBox="0 0 16 16" fill="none" stroke="#fff" stroke-width="1.4"><path d="M3 1l3 3-2 2c1 2 3 4 5 5l2-2 3 3-2 3C7 15 1 9 1 3z"/></svg>
        <p class="f-text">Telephone: +1 555 010 0139<br>Fax: +1 555 010 0142</p></div>
      <div class="f-row"><svg width="17" height="13" viewBox="0 0 17 13" fill="none" stroke="#fff" stroke-width="1.4"><rect x="1" y="1" width="15" height="11"/><path d="M1 1l7.5 6L16 1"/></svg>
        <p class="f-text">hello@kettlecast.example</p></div>
    </div>
    <div class="abs" style="left:328px;top:77px;width:290px">
      <h3>Sign up to receive email</h3>
      <p class="f-text" style="font-size:10.5px;line-height:18px;margin-top:12px">Excepteur sint occaecat cupidatat non proident, sunt in culpa qui Nemo enim ipsam voluptatem</p>
      <div class="f-input">Enter Name</div>
      <span class="f-btn">Subscribe</span>
    </div>
    <div class="abs" style="left:688px;top:77px;width:160px">
      <h3>Quick links</h3>
      <ul class="f-links"><li>Home</li><li>About Us</li><li>Podcast</li><li>Blog</li><li>Events</li><li>Contacts</li></ul>
    </div>
    <div class="abs f-brand">
      <div class="brand-dot" style="width:62px;height:62px"></div>
      <div class="brand-name">Before the kettle boils</div>
    </div>
    <p class="abs copyright">Copyright © Before the kettle boils 2017. All rights reserved.</p>
  </footer>
</div>
</body>
</html>
```